Brivolt Technologies business card design

We need a business card designed with our new logo. it would be great if the card could communicate it is a technology based company.

Target Market(s)

system integrators

Industry/Entity Type

technology, IOT

Contact Information for Business Card

Name, designation, Address, telephone number, email address

Requirements
Must have
• logo and company name
Nice to have
• something to do with technology

```html
<!DOCTYPE html>
<html lang="en">
<head>
<meta charset="utf-8">
<title>Brivolt Technologies – Business Card</title>
<link href="https://fonts.googleapis.com/css2?family=Inter:wght@400;600&display=swap" rel="stylesheet">
<style>
  :root {
    --stage: #2e2e2e;
    --card-light: #ffffff;
    --card-dark: #3f3f3f;
    --ink: #3d3d3d;
    --accent: #f7941d;
    --white: #ffffff;
  }
  * { margin: 0; padding: 0; box-sizing: border-box; }
  html, body {
    width: 1135px;
    height: 1200px;
    overflow: hidden;
    background: var(--stage);
    font-family: "Inter", sans-serif;
  }
  .canvas { position: relative; width: 1135px; height: 1200px; }

  .card {
    position: absolute;
    left: 205px;
    width: 726px;
    height: 415px;
  }
  .card--front { top: 145px; background: var(--card-light); }
  .card--back  { top: 641px; background: var(--card-dark); }

  /* Brand lockup */
  .brand {
    position: absolute;
    display: flex;
    align-items: center;
    gap: 14px;
    font-weight: 600;
  }
  .brand__square {
    width: 38px;
    height: 38px;
    background: var(--accent);
    flex: none;
  }
  .brand__name { line-height: 1; }
  .brand__main { display: block; letter-spacing: 0.5px; }
  .brand__sub  { display: block; letter-spacing: 6px; margin-top: 6px; }

  .card--front .brand { left: 47px; top: 181px; color: var(--ink); }
  .card--front .brand__main { font-size: 44px; }
  .card--front .brand__sub  { font-size: 15px; }

  .card--back .brand { left: 137px; top: 153px; color: var(--white); }
  .card--back .brand__square { width: 56px; height: 56px; }
  .card--back .brand__main { font-size: 62px; }
  .card--back .brand__sub  { font-size: 21px; letter-spacing: 9px; margin-top: 8px; }

  /* Contact block */
  .divider {
    position: absolute;
    left: 393px;
    top: 118px;
    width: 2px;
    height: 177px;
    background: var(--accent);
  }
  .contact {
    position: absolute;
    left: 422px;
    top: 112px;
    color: var(--ink);
  }
  .contact__name {
    font-size: 26px;
    font-weight: 600;
    color: var(--accent);
    line-height: 1.1;
  }
  .contact__role {
    font-size: 18px;
    font-weight: 400;
    margin-top: 3px;
    line-height: 1.2;
  }
  .contact__address {
    font-style: normal;
    font-size: 18px;
    line-height: 24px;
    margin-top: 9px;
  }
  .contact__list { list-style: none; margin-top: 4px; }
  .contact__item {
    display: flex;
    align-items: center;
    gap: 8px;
    font-size: 18px;
    line-height: 24.5px;
  }
  .contact__icon { width: 12px; height: 12px; flex: none; }
</style>
</head>
<body>
<div class="canvas">

  <section class="card card--front">
    <div class="brand">
      <span class="brand__square"></span>
      <span class="brand__name">
        <span class="brand__main">BRIVOLT</span>
        <span class="brand__sub">TECHNOLOGIES</span>
      </span>
    </div>

    <div class="divider"></div>

    <div class="contact">
      <h1 class="contact__name">DANIEL HARTWELL</h1>
      <p class="contact__role">DIRECTOR</p>
      <address class="contact__address">1420 Cedar Ridge Road<br>Lakeview, MI 48850</address>
      <ul class="contact__list">
        <li class="contact__item">
          <svg class="contact__icon" viewBox="0 0 12 12" aria-hidden="true"><path d="M3 1 L5 3.5 L4 5 Q5.5 7.5 7 8 L8.5 7 L11 9 L9.5 11 Q4 10 1 2.5 Z" fill="none" stroke="var(--accent)" stroke-width="1.2" stroke-linejoin="round"/></svg>
          <span>(555) 318-4072</span>
        </li>
        <li class="contact__item">
          <svg class="contact__icon" viewBox="0 0 12 12" aria-hidden="true"><rect x="0.8" y="2.3" width="10.4" height="7.4" fill="none" stroke="var(--accent)" stroke-width="1.1"/><path d="M1 2.6 L6 6.5 L11 2.6" fill="none" stroke="var(--accent)" stroke-width="1.1"/></svg>
          <span>info@brivolttech.com</span>
        </li>
        <li class="contact__item">
          <svg class="contact__icon" viewBox="0 0 12 12" aria-hidden="true"><g fill="none" stroke="var(--accent)" stroke-width="0.9"><circle cx="6" cy="6" r="5"/><ellipse cx="6" cy="6" rx="2.2" ry="5"/><path d="M1 6 H11 M1.8 3.5 H10.2 M1.8 8.5 H10.2"/></g></svg>
          <span>brivolttechnologies.com</span>
        </li>
      </ul>
    </div>
  </section>

  <section class="card card--back">
    <div class="brand">
      <span class="brand__square"></span>
      <span class="brand__name">
        <span class="brand__main">BRIVOLT</span>
        <span class="brand__sub">TECHNOLOGIES</span>
      </span>
    </div>
  </section>

</div>
</body>
</html>
```